need corporate, modern business card created for Consulting Company

I need a slick business card using elements from my website, as well as, integrating my pixelforge-created logo (see files).

The business card needs to be:
1. Corporate and modern
2. Clean and professional

I've included a PSD with the logo/icon that you can use to create it. Feel free to try a metallic finish on the logo, make it bigger/small, underlay it. Whatever you need to do to make my card stand out.

Try a black background, or white background or gray.

The idea is for my card to be memorable as well as professional and corporate.

Target Market(s)

Corporate business in the US and Canada.

Industry/Entity Type

Business

Contact Information for Business Card

Commerce Advancing Methods
Martin Coles, Senior Partner
office: 1 877 555 0143
mobile: 1 519 555 0172
website: http://www.brightvale.example

Requirements
Must have
• Card-related information
• corporate, yet modern
• clean and professional
• incorporate the icon only
• must have an editable form when complete!
Nice to have
• metallic icon might be cool
• try it with white or black

```html
<!DOCTYPE html>
<html lang="en">
<head>
<meta charset="utf-8">
<title>Brightvale Business Card</title>
<link rel="stylesheet" href="https://fonts.googleapis.com/css2?family=Open+Sans:wght@400;600;700&display=swap">
<style>
  :root {
    --stage: #e9eaec;
    --card-white: #ffffff;
    --card-grey: #eef0f2;
    --blue-light: #5aa5da;
    --blue-deep: #2f78bf;
    --ink: #1c1c1c;
    --text-grey: #333a40;
    --name-white: #ffffff;
  }
  html, body {
    margin: 0;
    padding: 0;
    width: 1200px;
    height: 885px;
    overflow: hidden;
    background: var(--stage);
    font-family: "Open Sans", Arial, sans-serif;
  }
  .stage {
    position: relative;
    width: 1200px;
    height: 885px;
  }
  .card {
    position: absolute;
    width: 680px;
    height: 389px;
    box-shadow: 0 10px 28px rgba(0,0,0,0.18);
  }
  .card svg { display: block; width: 100%; height: 100%; }
  .card--front { left: 260px; top: 34px; }
  .card--back  { left: 260px; top: 460px; }
  .brand-name {
    font-family: "Open Sans", Arial, sans-serif;
    font-weight: 700;
    fill: var(--blue-deep);
  }
  .holder-name { font-weight: 700; fill: var(--name-white); font-size: 26px; }
  .holder-role { font-weight: 400; fill: var(--name-white); font-size: 17px; opacity: .92; }
  .contact-line { font-weight: 400; fill: var(--text-grey); font-size: 17px; }
  .icon-box { fill: var(--blue-light); }
  .icon-glyph { fill: none; stroke: #fff; stroke-width: 1.6; stroke-linecap: round; stroke-linejoin: round; }
  .edge-line { fill: none; stroke: var(--ink); stroke-width: 4; }
</style>
</head>
<body>
<main class="stage">

  <section class="card card--front" aria-label="Business card front">
    <svg viewBox="0 0 680 389" xmlns="http://www.w3.org/2000/svg">
      <defs>
        <linearGradient id="blueBand" x1="0" y1="0" x2="1" y2="1">
          <stop offset="0" stop-color="var(--blue-light)"/>
          <stop offset="1" stop-color="var(--blue-deep)"/>
        </linearGradient>
        <linearGradient id="whitePanel" x1="0" y1="0" x2="1" y2="0">
          <stop offset="0" stop-color="var(--card-grey)"/>
          <stop offset="1" stop-color="var(--card-white)"/>
        </linearGradient>
      </defs>
      <rect class="card-base" width="680" height="389" fill="url(#blueBand)"/>
      <path class="white-panel" d="M0,0 H300 C430,0 530,110 530,220 C530,310 490,360 440,360 H0 Z" fill="url(#whitePanel)"/>
      <path class="edge-line" d="M300,0 C430,0 530,110 530,220 C530,310 490,360 440,360 H0"/>

      <text class="holder-name" x="662" y="52" text-anchor="end">Martin Coles</text>
      <text class="holder-role" x="662" y="76" text-anchor="end">Senior Partner</text>

      <circle cx="78" cy="172" r="16" fill="var(--blue-deep)"/>
      <text class="brand-name" x="106" y="192" font-size="56">brightvale</text>

      <g class="contact-block">
        <rect class="icon-box" x="60" y="236" width="20" height="20" rx="2"/>
        <path class="icon-glyph" d="M65,241 c1,5 4,9 10,10 l1.5,-2.5 -3,-2 -1.5,1.5 c-2,-1 -3,-2 -4,-4 l1.5,-1.5 -2,-3 z"/>
        <text class="contact-line" x="90" y="252">1 877 555 0143</text>

        <rect class="icon-box" x="60" y="264" width="20" height="20" rx="2"/>
        <rect class="icon-glyph" x="66" y="267.5" width="8" height="13" rx="1.5"/>
        <text class="contact-line" x="90" y="280">1 519 555 0172</text>

        <rect class="icon-box" x="60" y="292" width="20" height="20" rx="2"/>
        <path class="icon-glyph" d="M64,297 h12 v10 h-12 z M64,297 l6,5 6,-5"/>
        <text class="contact-line" x="90" y="308">info@brightvale.example</text>

        <rect class="icon-box" x="60" y="320" width="20" height="20" rx="2"/>
        <circle class="icon-glyph" cx="70" cy="330" r="6"/>
        <path class="icon-glyph" d="M64,330 h12 M70,324 c-3,3 -3,9 0,12 M70,324 c3,3 3,9 0,12"/>
        <text class="contact-line" x="90" y="336">www.brightvale.example</text>
      </g>
    </svg>
  </section>

  <section class="card card--back" aria-label="Business card back">
    <svg viewBox="0 0 680 389" xmlns="http://www.w3.org/2000/svg">
      <defs>
        <linearGradient id="backBand" x1="0" y1="0" x2="0" y2="1">
          <stop offset="0" stop-color="var(--blue-light)"/>
          <stop offset="1" stop-color="var(--blue-deep)"/>
        </linearGradient>
        <linearGradient id="backPanel" x1="0" y1="0" x2="1" y2="1">
          <stop offset="0" stop-color="var(--card-grey)"/>
          <stop offset="1" stop-color="var(--card-white)"/>
        </linearGradient>
      </defs>
      <rect class="card-base" width="680" height="389" fill="url(#backPanel)"/>
      <path class="side-band" d="M0,0 H150 C80,110 70,250 140,389 H0 Z" fill="url(#backBand)"/>
      <path class="edge-line" d="M150,0 C80,110 70,250 140,389"/>

      <circle cx="236" cy="193" r="20" fill="var(--blue-deep)"/>
      <text class="brand-name" x="270" y="216" font-size="66">brightvale</text>
    </svg>
  </section>

</main>
</body>
</html>
```